Business Card Design for Occupational Medicine Start Up Company

We need to design a professional business card. We are a healthcare company providing occupational medicine services to blue collar industries. We are professional, efficient and high quality service providers.

Target Market(s)

Blue Collar Industry: Shipbuilding, Ports, Trucking Companies; The Executives and Safety Officers for these companies

Industry/Entity Type

Healthcare

Contact Information for Business Card

Logo, Name, Title, Email, Phone

Other font styles liked:
• Please match our Brand Guide

Requirements
Must have
• Our Company Colors and Logo

```html
<!DOCTYPE html>
<html lang="en">
<head>
<meta charset="utf-8">
<title>CrewWell Clinics – Business Card</title>
<link rel="stylesheet" href="https://fonts.googleapis.com/css2?family=Montserrat:wght@400;500;700&display=swap">
<style>
  :root {
    --navy: #2e3470;
    --teal: #2a93a3;
    --orange: #e2a043;
    --card: #f7f8f9;
    --card-edge: #dfe2e6;
    --page: #e8e9ec;
    --text-soft: #3d4150;
    --mark-tint: #eef1f4;
  }
  * { margin: 0; padding: 0; box-sizing: border-box; }
  html, body {
    width: 1200px;
    height: 1200px;
    overflow: hidden;
    background: var(--page);
    font-family: "Montserrat", Arial, sans-serif;
  }
  .canvas {
    position: relative;
    width: 1200px;
    height: 1200px;
  }
  .business-card {
    position: absolute;
    left: 100px;
    top: 310px;
    width: 1000px;
    height: 580px;
    background: var(--card);
    border: 2px solid var(--card-edge);
    border-radius: 26px;
    box-shadow: 0 18px 40px rgba(40, 45, 70, 0.10);
    overflow: hidden;
  }
  .company-name {
    position: absolute;
    left: 56px;
    top: 60px;
    color: var(--navy);
    font-weight: 700;
    text-align: center;
    line-height: 1;
  }
  .company-name .line-main {
    display: block;
    font-size: 44px;
    letter-spacing: 1px;
  }
  .company-name .line-sub {
    display: block;
    margin-top: 10px;
    font-size: 22px;
    letter-spacing: 7px;
  }
  .person {
    position: absolute;
    left: 50px;
    top: 232px;
  }
  .person .accent-bar {
    position: absolute;
    left: -50px;
    top: 2px;
    width: 12px;
    height: 36px;
    background: var(--orange);
    border-radius: 0 6px 6px 0;
  }
  .person-name {
    color: var(--navy);
    font-size: 32px;
    font-weight: 700;
    letter-spacing: 0.5px;
  }
  .person-title {
    margin-top: 8px;
    color: var(--text-soft);
    font-size: 23px;
    font-weight: 500;
  }
  .contact-list {
    position: absolute;
    left: 50px;
    top: 372px;
    list-style: none;
  }
  .contact-list li {
    display: flex;
    align-items: center;
    height: 38px;
    color: var(--text-soft);
    font-size: 23px;
    font-weight: 500;
  }
  .contact-list svg {
    width: 22px;
    height: 22px;
    margin-right: 12px;
    flex: none;
  }
  .brand-mark-area {
    position: absolute;
    left: 500px;
    top: 45px;
    width: 440px;
    height: 440px;
    border-radius: 50%;
    background: var(--mark-tint);
  }
</style>
</head>
<body>
<main class="canvas">
  <section class="business-card">
    <div class="company-name">
      <span class="line-main">CREWWELL</span>
      <span class="line-sub">CLINICS</span>
    </div>

    <div class="person">
      <span class="accent-bar"></span>
      <p class="person-name">MARK ELLERY</p>
      <p class="person-title">President</p>
    </div>

    <ul class="contact-list">
      <li>
        <svg viewBox="0 0 24 24" aria-hidden="true"><path fill="var(--teal)" d="M6.6 10.8a15.1 15.1 0 0 0 6.6 6.6l2.2-2.2a1 1 0 0 1 1-.25 11.4 11.4 0 0 0 3.6.57 1 1 0 0 1 1 1V20a1 1 0 0 1-1 1A17 17 0 0 1 3 4a1 1 0 0 1 1-1h3.5a1 1 0 0 1 1 1c0 1.25.2 2.45.57 3.6a1 1 0 0 1-.25 1z"/></svg>
        555-014-2290
      </li>
      <li>
        <svg viewBox="0 0 24 24" aria-hidden="true"><rect x="2" y="5" width="20" height="14" rx="2" fill="var(--teal)"/><path d="M3 6l9 7 9-7" fill="none" stroke="var(--card)" stroke-width="2"/></svg>
        mark@crewwellclinics.com
      </li>
      <li>
        <svg viewBox="0 0 24 24" aria-hidden="true"><circle cx="12" cy="12" r="10" fill="none" stroke="var(--teal)" stroke-width="2.2"/><ellipse cx="12" cy="12" rx="4.2" ry="10" fill="none" stroke="var(--teal)" stroke-width="2"/><path d="M2.5 12h19" stroke="var(--teal)" stroke-width="2"/></svg>
        www.crewwellclinics.com
      </li>
    </ul>

    <div class="brand-mark-area"></div>
  </section>
</main>
</body>
</html>
```